Design Sales-Funnel page for our beauty brand*

Hi all,

we are a beauty brand located in Romania (Eastern-Europe) and we are using sales-funnel pages to sell our own make-up brushes.

We have a ready design (see download-link) that we are not totally happy with, so we want you to create a new version of it, which fits more to our companies website

www.lumavela.rowhich

is very clean and easy to read for our customers.

So, your task is to

1) re-create the main page of our sales funnel
2) according to your design from 1) create the upsell/downsell and thank-you page as well.

What we do not like about the actual design:
- it is not clean/simple enough = hard for the customer eye to catch the content. What do we mean with that? There are too many background frames, too many different colors used.
- The original price for our brushes is 1.299 LEI and for this sale, we are giving it away for 399 LEI (LEI = Romanian currency). The discount is 70%, but it does not show on the page enough.

You can download all files here:
https://www.filecrate-share.com/sh/4kqtpx2mw915bd/QXZrTnHvLpEeKcYwMbDoUfsJa?dl=0

Thanks,
Mirela

Target Market(s)

Women 18-35

Industry/Entity Type

Makeup

Number of Pages Required

4 page

Font styles to use
Sans Serif

Colors

Designer to choose colors to be used in the design.

Requirements
Must have
• See description
Nice to have
• See description
Should not have
• See description

```html
<!DOCTYPE html>
<html lang="en">
<head>
<meta charset="utf-8">
<title>Lumavela – Sales Funnel Page Concepts</title>
<link href="https://fonts.googleapis.com/css2?family=Playfair+Display:wght@700;900&family=Lato:wght@400;700;900&display=swap" rel="stylesheet">
<style>
  :root{
    --canvas:#f7dbe1;
    --ink:#2a2326;
    --muted:#7b7075;
    --paper:#ffffff;
    --soft:#fbf6f4;
    --footer:#1f1b1d;
  }
  .theme-amber{
    --accent:#f08b2d;
    --accent-soft:#fde7d2;
    --band:#f39a3c;
    --band-deep:#e67a1c;
    --photo-a:#e9c3a8;
    --photo-b:#b77c68;
  }
  .theme-rose{
    --accent:#cf6f8c;
    --accent-soft:#f8dde5;
    --band:#b3334d;
    --band-deep:#8c1f34;
    --photo-a:#f0c9cf;
    --photo-b:#c07f8c;
  }
  *{box-sizing:border-box;margin:0;padding:0}
  html,body{width:800px;height:1200px;overflow:hidden}
  body{background:var(--canvas);font-family:"Lato",Arial,sans-serif;color:var(--ink);position:relative}
  .page{position:absolute;top:15px;width:292px;height:1170px;background:var(--paper);overflow:hidden;box-shadow:0 4px 14px rgba(120,60,80,.18);display:flex;flex-direction:column}
  .page--left{left:98px}
  .page--right{left:412px}
  section,header,footer{position:relative;overflow:hidden;flex:none}
  .serif{font-family:"Playfair Display",Georgia,serif}
  .small{font-size:4.6px;line-height:1.55;color:var(--muted)}
  .btn{display:inline-block;background:var(--accent);color:#fff;font-size:4.8px;font-weight:700;letter-spacing:.4px;padding:4px 9px;text-transform:uppercase}
  .ph{display:block}

  /* nav */
  .nav{height:24px;display:flex;align-items:center;padding:0 12px;gap:8px;background:#fff}
  .brand{font-weight:900;font-size:7px;letter-spacing:.6px;color:var(--ink);display:flex;align-items:center;gap:3px}
  .brand-dot{width:5px;height:5px;border-radius:50%;background:var(--accent)}
  .nav-links{display:flex;gap:7px;margin-left:auto;font-size:4.3px;font-weight:700;color:var(--ink)}
  .nav .btn{padding:3px 6px;font-size:4px}

  /* hero */
  .hero{height:200px;display:flex}
  .hero-photo{width:130px;height:100%;background:linear-gradient(160deg,var(--photo-a),var(--photo-b))}
  .hero-copy{flex:1;padding:32px 14px 0 14px}
  .hero-copy h1{font-size:19px;line-height:1.02;font-weight:900;margin-bottom:8px}
  .hero-copy .small{margin-bottom:9px}
  .hero-dots{position:absolute;left:8px;bottom:14px;display:flex;gap:3px}
  .hero-dots i{width:4px;height:4px;border-radius:50%;background:#fff;opacity:.7}
  .hero-dots i:first-child{background:var(--accent);opacity:1}

  /* offer */
  .offer{height:125px;background:var(--soft);padding:22px 14px 0;display:flex;gap:10px;border-top:1px solid #f0e6e2}
  .offer-copy{flex:1}
  .offer-copy h2{font-size:7.6px;line-height:1.25;font-weight:900;margin-bottom:6px}
  .offer-copy .small{margin-bottom:8px}
  .offer-photo{width:92px;height:62px;background:linear-gradient(135deg,var(--accent-soft),var(--photo-b))}

  /* about */
  .about{height:150px;padding:28px 14px 0;display:flex;gap:12px}
  .about-art{width:118px;height:84px;background:linear-gradient(90deg,#2b2426,var(--accent) 55%,#e8d8d2)}
  .about-copy{flex:1;padding-top:6px}
  .about-copy h2{font-size:8px;font-weight:900;margin-bottom:6px;letter-spacing:.3px}

  /* why */
  .why{height:170px;background:linear-gradient(180deg,#fff,var(--accent-soft));padding:18px 14px 0}
  .why h2{font-size:8px;font-weight:900;margin-bottom:8px}
  .why h2 span{color:var(--accent)}
  .why-list{width:118px}
  .why-item{margin-bottom:8px}
  .why-item b{display:block;font-size:5px;margin-bottom:2px}
  .why-icons{position:absolute;left:150px;top:30px}
  .why-icons i{position:absolute;width:15px;height:15px;border-radius:50%;border:1px solid var(--accent);background:#fff}
  .why-face{position:absolute;right:-18px;top:58px;width:112px;height:112px;border-radius:50%;background:radial-gradient(circle at 40% 40%,var(--photo-a),var(--photo-b))}

  /* brand block */
  .brandline{height:60px;display:flex;align-items:center;padding-left:22px;background:var(--accent-soft)}
  .brandline .brand{font-size:15px;letter-spacing:1.5px;color:var(--accent)}
  .brandline .brand-dot{width:10px;height:10px}
  .brush-strip{height:50px;background:linear-gradient(100deg,#f4ece8,var(--photo-b) 50%,#2b2426)}

  /* reviews */
  .reviews{height:190px;padding:22px 14px 0;background:#fff}
  .reviews h2{font-size:8px;font-weight:900;text-align:center;margin-bottom:4px}
  .reviews > .small{text-align:center;margin:0 20px 14px}
  .review-card{display:flex;gap:8px;background:#fff;box-shadow:0 2px 8px rgba(0,0,0,.1);padding:10px;width:150px}
  .avatar{width:22px;height:22px;border-radius:50%;background:var(--accent-soft);flex:none}
  .review-card b{display:block;font-size:5px;margin-top:4px}
  .review-photo{position:absolute;right:14px;top:70px;width:100px;height:76px;background:linear-gradient(135deg,#d8e6df,var(--photo-a))}

  /* cta */
  .cta{height:95px;background:linear-gradient(90deg,var(--band),var(--band-deep));display:flex;align-items:center;padding:0 14px;gap:12px}
  .cta-book{width:46px;height:64px;background:linear-gradient(160deg,#fff,var(--accent-soft));box-shadow:2px 3px 6px rgba(0,0,0,.25)}
  .cta-copy h2{font-size:8.6px;line-height:1.2;font-weight:900;color:#fff;margin-bottom:5px}
  .cta-copy .btn{background:#fff;color:var(--band-deep)}

  /* footer */
  .footer{height:86px;background:var(--footer);padding:14px 14px 0;color:#fff}
  .footer-cols{display:flex;gap:14px}
  .footer-col{flex:1}
  .footer-col h3{font-size:5px;font-weight:900;margin-bottom:4px;letter-spacing:.4px}
  .footer-col p{font-size:4.3px;line-height:1.6;color:#b9b0b3}
  .footer-input{height:8px;background:#fff;margin:3px 0}
  .footer .brand{color:#fff;font-size:6px;margin-top:10px}
  .copyright{position:absolute;right:14px;bottom:10px;font-size:4px;color:#8f878a}
</style>
</head>
<body>

<!-- Variant one: amber accents -->
<article class="page page--left theme-amber">
  <header class="nav">
    <div class="brand"><span class="brand-dot"></span>LUMAVELA</div>
    <nav class="nav-links"><span>HOME</span><span>ABOUT</span><span>SHOP</span></nav>
    <span class="btn">Order</span>
  </header>
  <section class="hero">
    <div class="hero-photo ph" role="img" aria-label="Close-up photo of a model with bold make-up and painted nails"></div>
    <div class="hero-copy">
      <h1 class="serif">BETTER, FASTER MAKEUP</h1>
      <p class="small">Our soft brushes blend every product evenly, so your daily look is done in minutes. Made for beginners and pros alike, built to last for years of use.</p>
      <span class="btn">Get yours now</span>
    </div>
    <div class="hero-dots"><i></i><i></i><i></i></div>
  </section>
  <section class="offer">
    <div class="offer-copy">
      <h2 class="serif">THE 5 PIECE BRUSH SET ALL YOUR NEEDS, NOW AT A PRICE DISCOUNT</h2>
      <p class="small">Was 1.299 LEI, today only 399 LEI. Save 70% on the full set while stock lasts.</p>
      <span class="btn">Shop the set</span>
    </div>
    <div class="offer-photo ph" role="img" aria-label="Photo of a make-up brush sweeping powder across a cheek"></div>
  </section>
  <section class="about">
    <div class="about-art ph" role="img" aria-label="Arrangement of make-up brushes in graphic shapes"></div>
    <div class="about-copy">
      <h2 class="serif">ABOUT LUMAVELA</h2>
      <p class="small">We are a Romanian beauty brand creating tools that make make-up simple. Every brush is tested by artists and designed for clean, easy blending at home.</p>
    </div>
  </section>
  <section class="why">
    <h2 class="serif">WHY <span>LUMAVELA</span> BRUSHES?</h2>
    <div class="why-list">
      <div class="why-item"><b>Soft synthetic fibres</b><p class="small">Gentle on skin, no shedding, easy to wash.</p></div>
      <div class="why-item"><b>Flawless blending</b><p class="small">Even coverage with less product every day.</p></div>
      <div class="why-item"><b>Made to last</b><p class="small">Sturdy handles that keep their shape.</p></div>
    </div>
    <div class="why-icons"><i style="left:0;top:0"></i><i style="left:30px;top:-8px"></i><i style="left:-6px;top:36px"></i><i style="left:8px;top:70px"></i></div>
    <div class="why-face ph" role="img" aria-label="Round photo of a model with finished make-up"></div>
  </section>
  <section class="brandline"><div class="brand"><span class="brand-dot"></span>LUMAVELA</div></section>
  <section class="brush-strip ph" role="img" aria-label="Row of make-up brushes lying side by side"></section>
  <section class="reviews">
    <h2 class="serif">CUSTOMER REVIEWS</h2>
    <p class="small">Thousands of women already use our brushes every day. Here is what they say.</p>
    <div class="review-card">
      <div class="avatar ph" role="img" aria-label="Customer portrait"></div>
      <div><p class="small">"My foundation finally looks smooth. Best set I have ever owned!"</p><b>Ioana M.</b></div>
    </div>
    <div class="review-photo ph" role="img" aria-label="Photo of make-up products on a table"></div>
  </section>
  <section class="cta">
    <div class="cta-book ph" role="img" aria-label="Cover of the free make-up guide"></div>
    <div class="cta-copy">
      <h2 class="serif">FREE STEP BY STEP GUIDE TO PROFESSIONAL EVERYDAY MAKEUP</h2>
      <span class="btn">Download free</span>
    </div>
  </section>
  <footer class="footer">
    <div class="footer-cols">
      <div class="footer-col"><h3>CONTACT US</h3><p>Str. Florilor 12, Cluj<br>hello@lumavela.ro<br>+40 700 000 000</p></div>
      <div class="footer-col"><h3>QUICK LINKS</h3><p>Shop<br>About us<br>Shipping</p></div>
      <div class="footer-col"><h3>NEWSLETTER</h3><div class="footer-input"></div><span class="btn">Subscribe</span></div>
    </div>
    <div class="brand"><span class="brand-dot"></span>LUMAVELA</div>
    <p class="copyright">© Lumavela. All rights reserved.</p>
  </footer>
</article>

<!-- Variant two: rose accents -->
<article class="page page--right theme-rose">
  <header class="nav">
    <div class="brand"><span class="brand-dot"></span>LUMAVELA</div>
    <nav class="nav-links"><span>HOME</span><span>ABOUT</span><span>SHOP</span></nav>
    <span class="btn">Order</span>
  </header>
  <section class="hero">
    <div class="hero-photo ph" role="img" aria-label="Close-up photo of a model with bold make-up and painted nails"></div>
    <div class="hero-copy">
      <h1 class="serif">BETTER, FASTER MAKEUP</h1>
      <p class="small">Our soft brushes blend every product evenly, so your daily look is done in minutes. Made for beginners and pros alike, built to last for years of use.</p>
      <span class="btn">Get yours now</span>
    </div>
    <div class="hero-dots"><i></i><i></i><i></i></div>
  </section>
  <section class="offer">
    <div class="offer-copy">
      <h2 class="serif">THE 5 PIECE BRUSH SET ALL YOUR NEEDS, NOW AT A PRICE DISCOUNT</h2>
      <p class="small">Was 1.299 LEI, today only 399 LEI. Save 70% on the full set while stock lasts.</p>
      <span class="btn">Shop the set</span>
    </div>
    <div class="offer-photo ph" role="img" aria-label="Photo of a make-up brush sweeping powder across a cheek"></div>
  </section>
  <section class="about">
    <div class="about-art ph" role="img" aria-label="Arrangement of make-up brushes in graphic shapes"></div>
    <div class="about-copy">
      <h2 class="serif">ABOUT LUMAVELA</h2>
      <p class="small">We are a Romanian beauty brand creating tools that make make-up simple. Every brush is tested by artists and designed for clean, easy blending at home.</p>
    </div>
  </section>
  <section class="why">
    <h2 class="serif">WHY <span>LUMAVELA</span> BRUSHES?</h2>
    <div class="why-list">
      <div class="why-item"><b>Soft synthetic fibres</b><p class="small">Gentle on skin, no shedding, easy to wash.</p></div>
      <div class="why-item"><b>Flawless blending</b><p class="small">Even coverage with less product every day.</p></div>
      <div class="why-item"><b>Made to last</b><p class="small">Sturdy handles that keep their shape.</p></div>
    </div>
    <div class="why-icons"><i style="left:0;top:0"></i><i style="left:30px;top:-8px"></i><i style="left:-6px;top:36px"></i><i style="left:8px;top:70px"></i></div>
    <div class="why-face ph" role="img" aria-label="Round photo of a model with finished make-up"></div>
  </section>
  <section class="brandline"><div class="brand"><span class="brand-dot"></span>LUMAVELA</div></section>
  <section class="brush-strip ph" role="img" aria-label="Row of make-up brushes lying side by side"></section>
  <section class="reviews">
    <h2 class="serif">CUSTOMER REVIEWS</h2>
    <p class="small">Thousands of women already use our brushes every day. Here is what they say.</p>
    <div class="review-card">
      <div class="avatar ph" role="img" aria-label="Customer portrait"></div>
      <div><p class="small">"My foundation finally looks smooth. Best set I have ever owned!"</p><b>Ioana M.</b></div>
    </div>
    <div class="review-photo ph" role="img" aria-label="Photo of make-up products on a table"></div>
  </section>
  <section class="cta">
    <div class="cta-book ph" role="img" aria-label="Cover of the free make-up guide"></div>
    <div class="cta-copy">
      <h2 class="serif">FREE STEP BY STEP GUIDE TO PROFESSIONAL EVERYDAY MAKEUP</h2>
      <span class="btn">Download free</span>
    </div>
  </section>
  <footer class="footer">
    <div class="footer-cols">
      <div class="footer-col"><h3>CONTACT US</h3><p>Str. Florilor 12, Cluj<br>hello@lumavela.ro<br>+40 700 000 000</p></div>
      <div class="footer-col"><h3>QUICK LINKS</h3><p>Shop<br>About us<br>Shipping</p></div>
      <div class="footer-col"><h3>NEWSLETTER</h3><div class="footer-input"></div><span class="btn">Subscribe</span></div>
    </div>
    <div class="brand"><span class="brand-dot"></span>LUMAVELA</div>
    <p class="copyright">© Lumavela. All rights reserved.</p>
  </footer>
</article>

</body>
</html>
```